Logo, Web and Mobile Designs for enterprise social media platform

All the details are in the attached document, please start reading the scope document first which explains what is this project about and the details about the needed deliverables, after that please read the UI_Requirements document which will detail what is expected regarding the coded web version since this is a coded contest, it is very important that you meet the UI requirements or suggest something else but we will need to agree first before working on the coded version

Good Luck

Target Market(s)

Enterprise Social Media

Industry/Entity Type

Media

Coding

Coded - Design and coding required

Number of Pages Required

5+ page

Font styles to use
Sans Serif

Requirements
Must have
• All the must haves are listed in the scope document so please check before you start

```html
<!DOCTYPE html>
<html lang="en">
<head>
<meta charset="utf-8">
<title>Teamora – Home</title>
<link href="https://fonts.googleapis.com/css2?family=Bitter:wght@400;500&family=Open+Sans:wght@400;600;700&display=swap" rel="stylesheet">
<style>
:root{
  --blue:#0a78c3;
  --blue-dark:#0c5fa0;
  --lime:#a6c530;
  --ink:#333;
  --text:#555;
  --muted:#8a8a8a;
  --line:#e4e4e4;
  --bar:#f3f3f3;
  --topbar:#f0f0f0;
  --footer:#111;
}
*{box-sizing:border-box;margin:0;padding:0}
html,body{width:1200px;height:2493px;overflow:hidden;background:#fff}
body{position:relative;font-family:"Open Sans",Arial,sans-serif;color:var(--text);font-size:13px}
.slab{font-family:"Bitter",Georgia,serif}

/* top bar */
.topbar{position:absolute;left:0;top:0;width:1200px;height:68px;background:var(--topbar)}
.search{position:absolute;left:470px;top:21px;width:324px;height:33px;background:#fff;border:1px solid #e2e2e2}
.search span{position:absolute;left:14px;top:8px;font-size:11px;color:#bbb;font-style:italic}
.search-btn{position:absolute;right:-1px;top:-1px;width:33px;height:33px;background:var(--lime);display:flex;align-items:center;justify-content:center}
.alert{position:absolute;top:24px;width:26px;height:22px}
.alert .badge{position:absolute;left:14px;top:-10px;width:20px;height:20px;border-radius:50%;background:var(--blue);color:#fff;font-size:9px;font-weight:700;display:flex;align-items:center;justify-content:center}
.user-name{position:absolute;left:1039px;top:27px;font-size:12px;font-weight:700;color:#222}
.user-avatar{position:absolute;left:1084px;top:14px;width:40px;height:40px;border-radius:50%;background:linear-gradient(135deg,#b7b2ad,#6d6661);border:2px solid #fff}

/* header */
.header{position:absolute;left:0;top:68px;width:1200px;height:58px;background:#fff}
.logo-wave{position:absolute;left:0;top:100px;z-index:3}
.logo{position:absolute;left:76px;top:88px;z-index:4;font-family:"Bitter",Georgia,serif;font-size:34px;font-weight:500;color:var(--blue-dark)}
.nav{position:absolute;left:378px;top:68px;height:58px;display:flex;align-items:center}
.nav a{position:relative;display:block;padding:0 18px;font-size:13px;color:#222;text-decoration:none;border-left:1px solid #e6e6e6;line-height:18px}
.nav a:first-child{border-left:none;color:var(--blue)}
.nav a.active::before{content:"";position:absolute;left:0;right:0;top:-21px;height:4px;background:var(--blue)}
.nav a.active::after{content:"";position:absolute;left:50%;top:-17px;margin-left:-6px;border:6px solid transparent;border-top-color:var(--blue)}
.btn{position:absolute;top:83px;height:33px;color:#fff;font-size:11px;font-weight:700;text-transform:uppercase;display:flex;align-items:center;justify-content:center;font-family:"Bitter",Georgia,serif}
.btn-service{left:854px;width:162px;background:var(--blue)}
.btn-upgrade{left:1027px;width:100px;background:var(--lime)}

/* hero */
.hero{position:absolute;left:0;top:126px;width:1200px;height:562px;background:radial-gradient(ellipse at 52% 45%,#e7f2f4 0%,#a9ccd0 30%,#6e9ea8 60%,#47707e 100%)}
.hero-arrow{position:absolute;top:386px;width:50px;height:50px;border-radius:50%;background:#fff;box-shadow:0 1px 4px rgba(0,0,0,.35);display:flex;align-items:center;justify-content:center;z-index:2}

/* posts */
.posts{position:absolute;left:76px;top:751px;width:772px;display:flex;flex-direction:column;gap:28px}
.post{height:246px;border:1px solid var(--line);background:#fff}
.post-cat{height:43px;background:var(--bar);border-left:4px solid var(--blue);padding-left:14px;font-family:"Bitter",Georgia,serif;font-size:17px;color:#222;line-height:43px;margin-left:-1px;margin-top:-1px}
.post-body{position:relative;height:201px}
.post-img{position:absolute;left:16px;top:20px;width:193px;height:165px}
.post-title{position:absolute;left:234px;top:22px;font-family:"Bitter",Georgia,serif;font-size:18px;color:var(--blue-dark);font-weight:400}
.post-text{position:absolute;left:234px;top:56px;width:514px;font-size:12.4px;line-height:21px;text-align:justify;color:#555}
.post-meta{position:absolute;left:234px;top:165px;display:flex;gap:0;font-size:11.5px;color:var(--muted)}
.post-meta span{display:flex;align-items:center;gap:6px;width:125px}
.post-meta span:nth-child(2){width:125px}
.post-meta span:nth-child(3){width:95px}

/* sidebar */
.side-box{position:absolute;left:884px;width:243px;border:1px solid var(--line);background:#fff}
.side-title{font-family:"Bitter",Georgia,serif;color:var(--blue-dark);font-size:19px;font-weight:400}
.subscribe{top:751px;height:260px;padding:18px 17px}
.subscribe h3{font-family:"Bitter",Georgia,serif;color:var(--blue-dark);font-size:15px;font-weight:400}
.subscribe p{margin-top:6px;font-size:12px;line-height:18px;color:#555}
.field{margin-top:12px;height:33px;background:var(--bar);padding-left:16px;font-size:11px;line-height:33px;color:#aaa}
.field:first-of-type{margin-top:18px}
.submit{margin-top:13px;height:40px;background:var(--blue);color:#fff;font-size:12px;font-weight:700;text-align:center;line-height:40px;text-transform:uppercase}

.comments-title{position:absolute;left:884px;top:1050px}
.comment{position:absolute;left:884px;width:243px;height:120px}
.comment-img{position:absolute;left:0;top:2px;width:77px;height:59px}
.comment p{position:absolute;left:94px;top:0;width:149px;font-size:12px;line-height:21px;text-align:justify;color:#555}
.comment-stats{position:absolute;left:94px;top:67px;display:flex;gap:14px;font-size:11.5px;color:#555}
.comment-stats span{display:flex;align-items:center;gap:4px}
.comment-rule{position:absolute;left:94px;top:97px;width:149px;height:1px;background:var(--line)}

.notifications{top:1471px;height:299px;padding:16px 18px}
.note{display:flex;gap:12px;margin-top:18px;font-size:12px;line-height:20px;color:#555}
.note + .note{border-top:1px solid var(--line);padding-top:8px;margin-top:8px}
.note svg{flex:none;margin-top:4px}

.chat-title{position:absolute;left:884px;top:1804px}
.chat-people{position:absolute;left:884px;top:1838px;display:flex;gap:12px}
.chat-people div{width:50px;height:50px}

.profile-title{position:absolute;left:884px;top:1923px}
.profile{top:1998px;height:179px;text-align:center;padding:48px 18px 0}
.profile-avatar{position:absolute;left:972px;top:1962px;width:66px;height:66px;border-radius:50%;border:3px solid #fff;box-shadow:0 0 0 1px var(--line);background:linear-gradient(135deg,#e9e3dc,#a99d92);z-index:2}
.profile h4{font-family:"Bitter",Georgia,serif;color:var(--blue-dark);font-size:16px;font-weight:400;letter-spacing:1px}
.profile p{margin-top:6px;font-size:12px;line-height:20px;text-align:justify;text-align-last:center}
.profile a{display:block;margin-top:8px;font-size:12px;font-weight:700;color:var(--blue-dark);text-decoration:none}

/* footer */
.footer{position:absolute;left:0;top:2420px;width:1200px;height:73px;background:var(--footer)}
.footer p{position:absolute;left:76px;top:28px;font-size:11.5px;color:#888}
.social{position:absolute;left:986px;top:23px;display:flex;gap:13px}
.social span{width:25px;height:25px;border-radius:3px}
</style>
</head>
<body>

<div class="topbar">
  <div class="search"><span>Search here...</span>
    <div class="search-btn"><svg width="13" height="13" viewBox="0 0 13 13"><circle cx="5.5" cy="5.5" r="4" fill="none" stroke="#fff" stroke-width="2"/><line x1="8.5" y1="8.5" x2="12" y2="12" stroke="#fff" stroke-width="2"/></svg></div>
  </div>
  <div class="alert" style="left:846px"><svg width="24" height="18" viewBox="0 0 24 18"><rect x="1" y="1" width="22" height="16" rx="1" fill="#c3c3c3"/><path d="M1 1l11 9 11-9" fill="none" stroke="#f0f0f0" stroke-width="1.5"/></svg><span class="badge">12</span></div>
  <div class="alert" style="left:912px"><svg width="24" height="20" viewBox="0 0 24 20"><path d="M3 2h18a2 2 0 012 2v9a2 2 0 01-2 2H10l-5 4v-4H3a2 2 0 01-2-2V4a2 2 0 012-2z" fill="#c3c3c3"/></svg><span class="badge">02</span></div>
  <div class="alert" style="left:978px"><svg width="22" height="20" viewBox="0 0 22 20"><circle cx="11" cy="6" r="5" fill="#c3c3c3"/><path d="M1 20c0-6 4-8 10-8s10 2 10 8z" fill="#c3c3c3"/></svg><span class="badge">02</span></div>
  <div class="user-name">MAREK</div>
  <div class="user-avatar" role="img" aria-label="Portrait of the signed-in user"></div>
</div>

<div class="header"></div>
<svg class="logo-wave" width="290" height="70" viewBox="0 0 290 70" aria-hidden="true"><path d="M0 0H290C270 30 190 66 100 66 55 66 20 58 0 48Z" fill="#fff"/></svg>
<div class="logo">Teamora</div>
<nav class="nav">
  <a class="active">Home</a><a>About Us</a><a>Services</a><a>Blog</a><a>Contact Us</a>
</nav>
<div class="btn btn-service">Business Service</div>
<div class="btn btn-upgrade">Upgrade</div>

<div class="hero" role="img" aria-label="Hand holding a phone surrounded by glowing social network icons"></div>
<div class="hero-arrow" style="left:42px"><svg width="12" height="16" viewBox="0 0 12 16"><path d="M9 2L3 8l6 6" fill="none" stroke="#222" stroke-width="2.5"/></svg></div>
<div class="hero-arrow" style="left:1108px"><svg width="12" height="16" viewBox="0 0 12 16"><path d="M3 2l6 6-6 6" fill="none" stroke="#222" stroke-width="2.5"/></svg></div>

<main class="posts">
  <article class="post"><div class="post-cat">Events</div><div class="post-body">
    <div class="post-img" role="img" aria-label="Red push pins on a calendar" style="background:linear-gradient(135deg,#d9d9d9,#b84a4a 55%,#8f8f8f)"></div>
    <h2 class="post-title">de Finibus Bonorum et Malorum</h2>
    <p class="post-text">Lorem ipsum dolor sit amet, consectetur adipiscing elit, sed do eiusmod tempor incididunt ut labore et dolore magna aliqua. Ut enim ad minim veniam, quis nostrud exercitation ullamco laboris nisi ut aliquip ex ea commodo consequat. Duis aute irure dolor in reprehenderit in voluptate velit esse cillum dolore.</p>
    <div class="post-meta"><span><svg width="10" height="11"><circle cx="5" cy="3" r="3" fill="#0a78c3"/><path d="M0 11c0-4 2-5 5-5s5 1 5 5z" fill="#0a78c3"/></svg>Post by Admin</span><span><svg width="13" height="11"><ellipse cx="6.5" cy="5" rx="6" ry="4.5" fill="#0a78c3"/><path d="M2 8l-1 3 4-2z" fill="#0a78c3"/></svg>Comments</span><span><svg width="11" height="11"><path d="M0 5h2v6H0zM3 5l3-5c1 0 2 1 1.5 3H11l-1 8H3z" fill="none" stroke="#0a78c3" stroke-width="1.2"/></svg>Likes</span><span><svg width="11" height="11"><circle cx="2" cy="5.5" r="2" fill="#0a78c3"/><circle cx="9" cy="2" r="2" fill="#0a78c3"/><circle cx="9" cy="9" r="2" fill="#0a78c3"/><path d="M2 5.5L9 2M2 5.5L9 9" stroke="#0a78c3"/></svg>Share</span></div>
  </div></article>

  <article class="post"><div class="post-cat">Business</div><div class="post-body">
    <div class="post-img" role="img" aria-label="Two businessmen looking at a tablet" style="background:linear-gradient(135deg,#e8edf2,#5c6f86 60%,#26344a)"></div>
    <h2 class="post-title">de Finibus Bonorum et Malorum</h2>
    <p class="post-text">Lorem ipsum dolor sit amet, consectetur adipiscing elit, sed do eiusmod tempor incididunt ut labore et dolore magna aliqua. Ut enim ad minim veniam, quis nostrud exercitation ullamco laboris nisi ut aliquip ex ea commodo consequat. Duis aute irure dolor in reprehenderit in voluptate velit esse cillum dolore.</p>
    <div class="post-meta"><span><svg width="10" height="11"><circle cx="5" cy="3" r="3" fill="#0a78c3"/><path d="M0 11c0-4 2-5 5-5s5 1 5 5z" fill="#0a78c3"/></svg>Post by Admin</span><span><svg width="13" height="11"><ellipse cx="6.5" cy="5" rx="6" ry="4.5" fill="#0a78c3"/><path d="M2 8l-1 3 4-2z" fill="#0a78c3"/></svg>Comments</span><span><svg width="11" height="11"><path d="M0 5h2v6H0zM3 5l3-5c1 0 2 1 1.5 3H11l-1 8H3z" fill="none" stroke="#0a78c3" stroke-width="1.2"/></svg>Likes</span><span><svg width="11" height="11"><circle cx="2" cy="5.5" r="2" fill="#0a78c3"/><circle cx="9" cy="2" r="2" fill="#0a78c3"/><circle cx="9" cy="9" r="2" fill="#0a78c3"/><path d="M2 5.5L9 2M2 5.5L9 9" stroke="#0a78c3"/></svg>Share</span></div>
  </div></article>

  <article class="post"><div class="post-cat">Features</div><div class="post-body">
    <div class="post-img" role="img" aria-label="Hand holding a glowing globe with app icons" style="background:radial-gradient(circle at 50% 55%,#6fb6e6,#2d4d6e 55%,#c9d3dc)"></div>
    <h2 class="post-title">de Finibus Bonorum et Malorum</h2>
    <p class="post-text">Lorem ipsum dolor sit amet, consectetur adipiscing elit, sed do eiusmod tempor incididunt ut labore et dolore magna aliqua. Ut enim ad minim veniam, quis nostrud exercitation ullamco laboris nisi ut aliquip ex ea commodo consequat. Duis aute irure dolor in reprehenderit in voluptate velit esse cillum dolore.</p>
    <div class="post-meta"><span><svg width="10" height="11"><circle cx="5" cy="3" r="3" fill="#0a78c3"/><path d="M0 11c0-4 2-5 5-5s5 1 5 5z" fill="#0a78c3"/></svg>Post by Admin</span><span><svg width="13" height="11"><ellipse cx="6.5" cy="5" rx="6" ry="4.5" fill="#0a78c3"/><path d="M2 8l-1 3 4-2z" fill="#0a78c3"/></svg>Comments</span><span><svg width="11" height="11"><path d="M0 5h2v6H0zM3 5l3-5c1 0 2 1 1.5 3H11l-1 8H3z" fill="none" stroke="#0a78c3" stroke-width="1.2"/></svg>Likes</span><span><svg width="11" height="11"><circle cx="2" cy="5.5" r="2" fill="#0a78c3"/><circle cx="9" cy="2" r="2" fill="#0a78c3"/><circle cx="9" cy="9" r="2" fill="#0a78c3"/><path d="M2 5.5L9 2M2 5.5L9 9" stroke="#0a78c3"/></svg>Share</span></div>
  </div></article>

  <article class="post"><div class="post-cat">Networks</div><div class="post-body">
    <div class="post-img" role="img" aria-label="Small figures connected in a network" style="background:linear-gradient(135deg,#eef0f2,#9aa6b2 60%,#5a6672)"></div>
    <h2 class="post-title">de Finibus Bonorum et Malorum</h2>
    <p class="post-text">Lorem ipsum dolor sit amet, consectetur adipiscing elit, sed do eiusmod tempor incididunt ut labore et dolore magna aliqua. Ut enim ad minim veniam, quis nostrud exercitation ullamco laboris nisi ut aliquip ex ea commodo consequat. Duis aute irure dolor in reprehenderit in voluptate velit esse cillum dolore.</p>
    <div class="post-meta"><span><svg width="10" height="11"><circle cx="5" cy="3" r="3" fill="#0a78c3"/><path d="M0 11c0-4 2-5 5-5s5 1 5 5z" fill="#0a78c3"/></svg>Post by Admin</span><span><svg width="13" height="11"><ellipse cx="6.5" cy="5" rx="6" ry="4.5" fill="#0a78c3"/><path d="M2 8l-1 3 4-2z" fill="#0a78c3"/></svg>Comments</span><span><svg width="11" height="11"><path d="M0 5h2v6H0zM3 5l3-5c1 0 2 1 1.5 3H11l-1 8H3z" fill="none" stroke="#0a78c3" stroke-width="1.2"/></svg>Likes</span><span><svg width="11" height="11"><circle cx="2" cy="5.5" r="2" fill="#0a78c3"/><circle cx="9" cy="2" r="2" fill="#0a78c3"/><circle cx="9" cy="9" r="2" fill="#0a78c3"/><path d="M2 5.5L9 2M2 5.5L9 9" stroke="#0a78c3"/></svg>Share</span></div>
  </div></article>

  <article class="post"><div class="post-cat">Business</div><div class="post-body">
    <div class="post-img" role="img" aria-label="Business team in a meeting" style="background:linear-gradient(135deg,#f2f4f6,#a8b4c2 55%,#2f3a48)"></div>
    <h2 class="post-title">de Finibus Bonorum et Malorum</h2>
    <p class="post-text">Lorem ipsum dolor sit amet, consectetur adipiscing elit, sed do eiusmod tempor incididunt ut labore et dolore magna aliqua. Ut enim ad minim veniam, quis nostrud exercitation ullamco laboris nisi ut aliquip ex ea commodo consequat. Duis aute irure dolor in reprehenderit in voluptate velit esse cillum dolore.</p>
    <div class="post-meta"><span><svg width="10" height="11"><circle cx="5" cy="3" r="3" fill="#0a78c3"/><path d="M0 11c0-4 2-5 5-5s5 1 5 5z" fill="#0a78c3"/></svg>Post by Admin</span><span><svg width="13" height="11"><ellipse cx="6.5" cy="5" rx="6" ry="4.5" fill="#0a78c3"/><path d="M2 8l-1 3 4-2z" fill="#0a78c3"/></svg>Comments</span><span><svg width="11" height="11"><path d="M0 5h2v6H0zM3 5l3-5c1 0 2 1 1.5 3H11l-1 8H3z" fill="none" stroke="#0a78c3" stroke-width="1.2"/></svg>Likes</span><span><svg width="11" height="11"><circle cx="2" cy="5.5" r="2" fill="#0a78c3"/><circle cx="9" cy="2" r="2" fill="#0a78c3"/><circle cx="9" cy="9" r="2" fill="#0a78c3"/><path d="M2 5.5L9 2M2 5.5L9 9" stroke="#0a78c3"/></svg>Share</span></div>
  </div></article>

  <article class="post"><div class="post-cat">Events</div><div class="post-body">
    <div class="post-img" role="img" aria-label="Two people chatting over coffee at a cafe" style="background:linear-gradient(135deg,#d8c7b2,#9a6f4e 55%,#3d3a3a)"></div>
    <h2 class="post-title">de Finibus Bonorum et Malorum</h2>
    <p class="post-text">Lorem ipsum dolor sit amet, consectetur adipiscing elit, sed do eiusmod tempor incididunt ut labore et dolore magna aliqua. Ut enim ad minim veniam, quis nostrud exercitation ullamco laboris nisi ut aliquip ex ea commodo consequat. Duis aute irure dolor in reprehenderit in voluptate velit esse cillum dolore.</p>
    <div class="post-meta"><span><svg width="10" height="11"><circle cx="5" cy="3" r="3" fill="#0a78c3"/><path d="M0 11c0-4 2-5 5-5s5 1 5 5z" fill="#0a78c3"/></svg>Post by Admin</span><span><svg width="13" height="11"><ellipse cx="6.5" cy="5" rx="6" ry="4.5" fill="#0a78c3"/><path d="M2 8l-1 3 4-2z" fill="#0a78c3"/></svg>Comments</span><span><svg width="11" height="11"><path d="M0 5h2v6H0zM3 5l3-5c1 0 2 1 1.5 3H11l-1 8H3z" fill="none" stroke="#0a78c3" stroke-width="1.2"/></svg>Likes</span><span><svg width="11" height="11"><circle cx="2" cy="5.5" r="2" fill="#0a78c3"/><circle cx="9" cy="2" r="2" fill="#0a78c3"/><circle cx="9" cy="9" r="2" fill="#0a78c3"/><path d="M2 5.5L9 2M2 5.5L9 9" stroke="#0a78c3"/></svg>Share</span></div>
  </div></article>
</main>

<aside>
  <div class="side-box subscribe">
    <h3>Add/Subscribe to events</h3>
    <p>Ut enim ad minim veniam, quis nostrud exercitation</p>
    <div class="field">Name:*</div>
    <div class="field">Email:*</div>
    <div class="submit">Submit Here</div>
  </div>

  <h3 class="side-title comments-title">Post Comments</h3>
  <div class="comment" style="top:1092px">
    <div class="comment-img" role="img" aria-label="Pen resting on documents" style="background:linear-gradient(135deg,#f4f4f4,#b9bfc6)"></div>
    <p>Ut enim situ ead minim veniam, quis nostrud exercitationp</p>
    <div class="comment-stats"><span><svg width="12" height="10"><ellipse cx="6" cy="4.5" rx="5.5" ry="4" fill="#0a78c3"/></svg>(12)</span><span><svg width="11" height="11"><path d="M0 5h2v6H0zM3 5l3-5c1 0 2 1 1.5 3H11l-1 8H3z" fill="none" stroke="#0a78c3" stroke-width="1.2"/></svg>(3)</span></div>
    <div class="comment-rule"></div>
  </div>
  <div class="comment" style="top:1214px">
    <div class="comment-img" role="img" aria-label="Two colleagues talking" style="background:linear-gradient(135deg,#e2c9b4,#7b8ea6)"></div>
    <p>Ut enim situ ead minim veniam, quis nostrud exercitationp</p>
    <div class="comment-stats"><span><svg width="12" height="10"><ellipse cx="6" cy="4.5" rx="5.5" ry="4" fill="#0a78c3"/></svg>(12)</span><span><svg width="11" height="11"><path d="M0 5h2v6H0zM3 5l3-5c1 0 2 1 1.5 3H11l-1 8H3z" fill="none" stroke="#0a78c3" stroke-width="1.2"/></svg>(3)</span></div>
    <div class="comment-rule"></div>
  </div>
  <div class="comment" style="top:1336px">
    <div class="comment-img" role="img" aria-label="Glowing yellow light bulb" style="background:radial-gradient(circle at 50% 50%,#f5e27a,#d9c23a 45%,#f2f2f2 75%)"></div>
    <p>Ut enim situ ead minim veniam, quis nostrud exercitationp</p>
    <div class="comment-stats"><span><svg width="12" height="10"><ellipse cx="6" cy="4.5" rx="5.5" ry="4" fill="#0a78c3"/></svg>(12)</span><span><svg width="11" height="11"><path d="M0 5h2v6H0zM3 5l3-5c1 0 2 1 1.5 3H11l-1 8H3z" fill="none" stroke="#0a78c3" stroke-width="1.2"/></svg>(3)</span></div>
  </div>

  <div class="side-box notifications">
    <h3 class="side-title">Notifications</h3>
    <div class="note"><svg width="26" height="20" viewBox="0 0 26 20"><ellipse cx="10" cy="8" rx="9" ry="7" fill="#0a78c3"/><path d="M4 13l-2 5 6-3z" fill="#0a78c3"/><ellipse cx="18" cy="12" rx="7" ry="5.5" fill="#0a78c3" stroke="#fff" stroke-width="1.5"/></svg><span>Lorem ipsum dolor sit amet, consectetur adipiscing elit, sed do eiusmod.</span></div>
    <div class="note"><svg width="26" height="20" viewBox="0 0 26 20"><ellipse cx="10" cy="8" rx="9" ry="7" fill="#0a78c3"/><path d="M4 13l-2 5 6-3z" fill="#0a78c3"/><ellipse cx="18" cy="12" rx="7" ry="5.5" fill="#0a78c3" stroke="#fff" stroke-width="1.5"/></svg><span>Lorem ipsum dolor sit amet, consectetur adipiscing elit, sed do eiusmod.</span></div>
    <div class="note"><svg width="26" height="20" viewBox="0 0 26 20"><ellipse cx="10" cy="8" rx="9" ry="7" fill="#0a78c3"/><path d="M4 13l-2 5 6-3z" fill="#0a78c3"/><ellipse cx="18" cy="12" rx="7" ry="5.5" fill="#0a78c3" stroke="#fff" stroke-width="1.5"/></svg><span>Lorem ipsum dolor sit amet, consectetur adipiscing elit, sed do eiusmod.</span></div>
  </div>

  <h3 class="side-title chat-title">Chat</h3>
  <div class="chat-people">
    <div role="img" aria-label="Chat contact portrait" style="background:linear-gradient(135deg,#e6d2bd,#a88662)"></div>
    <div role="img" aria-label="Chat contact portrait" style="background:linear-gradient(135deg,#d9b59a,#6b5446)"></div>
    <div role="img" aria-label="Chat contact portrait" style="background:linear-gradient(135deg,#8a6a55,#3a2c24)"></div>
    <div role="img" aria-label="Chat contact portrait" style="background:linear-gradient(135deg,#d8d2cc,#5d5a60)"></div>
  </div>

  <h3 class="side-title profile-title">User Profile</h3>
  <div class="profile-avatar" role="img" aria-label="Profile portrait"></div>
  <div class="side-box profile">
    <h4>TOBIN</h4>
    <p>Lorem ipsum dolor sit amet, consectetur adipiscing elit, sed do labore et dolore magna.</p>
    <a>Read More</a>
  </div>
</aside>

<footer class="footer">
  <p>© 2015, Yoursite, All Right Reserved.</p>
  <div class="social" aria-label="Social links">
    <span style="background:#3b5a9a"></span>
    <span style="background:#2a9fd8"></span>
    <span style="background:#d6452f"></span>
    <span style="background:#3d6e96"></span>
  </div>
</footer>

</body>
</html>
```